U.S. Popcorn company needs business cards

We are a popcorn company that manufactures popcorn and sells it to grocery stores worldwide. Our theme is "Americana" and our logo is U.S. route 66 which is the most famous highway in the U.S.

We would like the design to be simple and to use both sides. On the back side we would like to see just the logo and website. The front would be normal details

Target Market(s)

Wholesalers, grocers and distributors

Industry/Entity Type

Manufacture

Contact Information for Business Card

Business name: Prairie Lantern Popcorn
Phone: +1 555 308 4726
Email: Dale@prairielanternpopcorn.com
website: www.prairielanternpopcorn.com
Tag Line: "Fresh for the long road"
Name: Dale Whitcombe
Title: Founder/President

Requirements
Must have
• Either this design should be fun or clean and simple. I will let you show me your thougths.
Nice to have
• Anything that ties in the real Hwy Route 66.
• Colors might need to be red, white and blue incorporated.
Should not have
• Not be too busy.

```html
<!DOCTYPE html>
<html lang="en">
<head>
<meta charset="utf-8">
<title>Prairie Lantern Popcorn – Business Cards</title>
<link href="https://fonts.googleapis.com/css2?family=Source+Sans+3:ital,wght@0,400;0,600;0,700;1,600&display=swap" rel="stylesheet">
<style>
  :root {
    --navy: #052566;
    --red: #e0202a;
    --white: #ffffff;
    --backdrop: #5b4a3a;
  }
  * { box-sizing: border-box; margin: 0; padding: 0; }
  html, body {
    width: 1200px;
    height: 987px;
    overflow: hidden;
  }
  body {
    background: var(--backdrop);
    font-family: "Source Sans 3", "Myriad Pro", Arial, sans-serif;
    position: relative;
  }
  .card {
    position: absolute;
    left: 293px;
    width: 615px;
    height: 351px;
    overflow: hidden;
    box-shadow: 0 2px 6px rgba(0,0,0,0.35);
  }
  .card--front { top: 130px; background: var(--white); }
  .card--back  { top: 505px; background: var(--navy); }

  .front-shape {
    position: absolute;
    inset: 0;
    width: 100%;
    height: 100%;
  }

  .brand {
    position: absolute;
    display: flex;
    flex-direction: column;
    align-items: center;
    gap: 8px;
    text-align: center;
    font-weight: 700;
    text-transform: uppercase;
    line-height: 1.05;
  }
  .brand__dot {
    width: 14px;
    height: 14px;
    border-radius: 50%;
    background: var(--red);
  }
  .card--front .brand {
    left: 24px;
    top: 110px;
    width: 220px;
    color: var(--navy);
    font-size: 30px;
  }
  .card--back .brand {
    left: 0;
    right: 0;
    top: 98px;
    color: var(--white);
    font-size: 34px;
  }

  .person {
    position: absolute;
    left: 345px;
    top: 88px;
  }
  .person__name {
    color: var(--red);
    font-size: 31px;
    font-weight: 600;
    line-height: 1;
  }
  .person__title {
    color: var(--white);
    font-size: 23px;
    font-weight: 400;
    margin-top: 8px;
  }

  .contact {
    position: absolute;
    right: 28px;
    top: 186px;
    list-style: none;
    color: var(--white);
    font-size: 15.5px;
  }
  .contact__item {
    display: flex;
    justify-content: flex-end;
    align-items: center;
    gap: 10px;
    height: 23px;
  }
  .contact__icon {
    width: 14px;
    height: 14px;
    fill: var(--red);
    flex: none;
  }

  .tagline {
    position: absolute;
    left: 0;
    right: 0;
    top: 298px;
    text-align: center;
    color: var(--white);
    font-size: 18px;
    font-style: italic;
    font-weight: 600;
  }
</style>
</head>
<body>

<section class="card card--front" aria-label="Business card front">
  <svg class="front-shape" viewBox="0 0 525 300" preserveAspectRatio="none" aria-hidden="true">
    <path d="M205 0 C225 20 250 35 258 50 C245 70 232 100 236 160 C240 230 200 270 140 285 C125 290 115 295 110 300 L525 300 L525 0 Z" fill="var(--navy)"/>
    <path d="M205 0 C225 20 250 35 258 50 C245 70 232 100 236 160 C240 230 200 270 140 285 C125 290 115 295 110 300" fill="none" stroke="var(--red)" stroke-width="3"/>
  </svg>

  <div class="brand">
    <span class="brand__dot"></span>
    <span>Prairie Lantern Popcorn</span>
  </div>

  <div class="person">
    <p class="person__name">Dale Whitcombe</p>
    <p class="person__title">Founder/President</p>
  </div>

  <ul class="contact">
    <li class="contact__item">
      <span>+1 555 308 4726</span>
      <svg class="contact__icon" viewBox="0 0 24 24" aria-hidden="true"><path d="M6.6 10.8a15.1 15.1 0 0 0 6.6 6.6l2.2-2.2c.3-.3.7-.4 1-.2 1.1.4 2.3.6 3.6.6.6 0 1 .4 1 1V20c0 .6-.4 1-1 1A17 17 0 0 1 3 4c0-.6.4-1 1-1h3.5c.6 0 1 .4 1 1 0 1.3.2 2.5.6 3.6.1.3 0 .7-.2 1z"/></svg>
    </li>
    <li class="contact__item">
      <span>Dale@prairielanternpopcorn.com</span>
      <svg class="contact__icon" viewBox="0 0 24 24" aria-hidden="true"><path d="M2 5h20v14H2z M2 5l10 8 10-8" fill="var(--red)" stroke="var(--navy)" stroke-width="1.5"/></svg>
    </li>
    <li class="contact__item">
      <span>www.prairielanternpopcorn.com</span>
      <svg class="contact__icon" viewBox="0 0 24 24" aria-hidden="true"><circle cx="12" cy="12" r="10"/><path d="M2 12h20M12 2c3 3 3 17 0 20M12 2c-3 3-3 17 0 20" fill="none" stroke="var(--navy)" stroke-width="1.5"/></svg>
    </li>
  </ul>
</section>

<section class="card card--back" aria-label="Business card back">
  <div class="brand">
    <span class="brand__dot"></span>
    <span>Prairie Lantern<br>Popcorn</span>
  </div>
  <p class="tagline">Fresh for the long road</p>
</section>

</body>
</html>
```